Visitenkarten-Design für Steuerberater und Wirtschaftsprüfer
Thank you so much! Great communication, very fast and nice contact!
Zielgruppe
Steuerberater, Wirtschaftsprüfer in München
Aufgabenstellung
Wir haben ein Logo das uns gefällt, jetzt allerdings steht die Umfirmierung vor der Tür und aus der Kanzlei Zelliger (so unser Name) wird Zelliger und Partner mbB (die Jugend kommt mit als Partner in die Kanzlei) , Steuerberater, Wirtschaftsprüfer
Analog unseres alten Briefpapiers und der alten Visitenkarten soll eigentlich nur der Zusatz 'und Partner mbB' oder '& Partner mbB' gestaltet werden.
Das Dateiformat bei Visitenkarten bitte so übergeben, dass wir Namen selbst austauschen mit gängigen Officeprogrammen austauschen können. Bei den Visitenkarten ist das große 'Zelliger' geprägt.
Ich stelle das Logo, das aktuelle Briefpapier und aktuelle Visitenkarten ein. Unsere Farbe ist grau.
Das Logo bitte in .pdf, .png, .psd und .eps (sagt mi alles nichts, haben wir aber alles schon mal irgendwo gebraucht) , Visiten karten auch in .pddf und .ai
Bei Fragen kontaktiert mich gern jederzeit.

```html
<!DOCTYPE html>
<html lang="de">
<head>
<meta charset="utf-8">
<title>Zelliger und Partner mbB – Visitenkarte</title>
<link href="https://fonts.googleapis.com/css2?family=Arimo:wght@400;700&display=swap" rel="stylesheet">
<style>
  :root {
    --backdrop: #1c1c1c;
    --card: #5b5b5b;
    --emboss: #7d7d7d;
    --emboss-line: #747474;
    --ink: #ffffff;
    --ink-soft: #e4e4e4;
  }
  * { box-sizing: border-box; margin: 0; padding: 0; }
  html, body { width: 1200px; height: 900px; overflow: hidden; }
  body {
    background: var(--backdrop);
    font-family: "Arimo", Arial, sans-serif;
    position: relative;
  }
  .card {
    position: absolute;
    top: 300px;
    width: 520px;
    height: 300px;
    background: var(--card);
    box-shadow: 0 12px 30px rgba(0,0,0,.55);
  }
  .card--front { left: 60px; }
  .card--back { left: 620px; }

  /* Vorderseite */
  .front-mark__name {
    position: absolute;
    left: 0; right: 0; top: 96px;
    text-align: center;
    white-space: nowrap;
    color: var(--emboss);
    font-size: 30px;
    line-height: 36px;
    font-weight: 700;
    letter-spacing: 1px;
  }
  .front-mark__tagline {
    position: absolute;
    left: 0; right: 0; top: 146px;
    text-align: center;
    white-space: nowrap;
    color: var(--emboss);
    font-size: 13px;
    line-height: 16px;
    letter-spacing: 1.5px;
    text-transform: uppercase;
  }
  .front-rule {
    position: absolute;
    height: 1px;
    background: var(--emboss-line);
  }
  .front-rule--top { left: 300px; right: 30px; top: 70px; }
  .front-rule--bottom { left: 30px; right: 300px; bottom: 40px; }
  .front-web {
    position: absolute;
    left: 0; right: 0; top: 196px;
    text-align: center;
    white-space: nowrap;
    font-size: 11px;
    line-height: 14px;
    letter-spacing: .5px;
    color: var(--emboss);
  }

  /* Rückseite */
  .back-mark {
    position: absolute;
    right: 30px; top: 32px;
    text-align: right;
    white-space: nowrap;
    color: var(--ink);
  }
  .back-mark__name { font-size: 20px; font-weight: 700; letter-spacing: 1px; }
  .back-mark__tagline {
    margin-top: 4px;
    font-size: 8px;
    letter-spacing: 1px;
    text-transform: uppercase;
  }
  .person { position: absolute; left: 34px; top: 112px; color: var(--ink); }
  .person__name { font-size: 20px; line-height: 24px; font-weight: 400; }
  .person__role { margin-top: 4px; font-size: 8.5px; line-height: 1.45; color: var(--ink-soft); }
  .back-rule {
    position: absolute;
    left: 34px; right: 30px;
    height: 1px;
    background: var(--ink);
  }
  .back-rule--upper { top: 194px; }
  .back-rule--lower { top: 240px; }
  .contact {
    position: absolute;
    display: flex;
    align-items: center;
    gap: 6px;
    white-space: nowrap;
    font-size: 10.5px;
    line-height: 14px;
    color: var(--ink);
  }
  .contact svg { width: 10px; height: 10px; fill: var(--ink); flex: none; }
  .contact--address { left: 34px; top: 211px; }
  .contact--fax { left: 260px; top: 211px; }
  .contact--mail { left: 370px; top: 211px; }
  .contact--phone { left: 34px; top: 258px; }
</style>
</head>
<body>

<section class="card card--front" aria-label="Vorderseite">
  <div class="front-rule front-rule--top"></div>
  <div class="front-mark__name">ZELLIGER &amp; Partner mbB</div>
  <div class="front-mark__tagline">Steuerberater | Wirtschaftsprüfer</div>
  <div class="front-web">www.kanzlei-zelliger.com</div>
  <div class="front-rule front-rule--bottom"></div>
</section>

<section class="card card--back" aria-label="Rückseite">
  <div class="back-mark">
    <div class="back-mark__name">ZELLIGER &amp; Partner mbB</div>
    <div class="back-mark__tagline">Steuerberater | Wirtschaftsprüfer</div>
  </div>

  <div class="person">
    <div class="person__name">Lorenz K. Zelliger</div>
    <div class="person__role">Dipl.-Kfm.<br>Steuerberater<br>Wirtschaftsprüfer</div>
  </div>

  <div class="back-rule back-rule--upper"></div>

  <div class="contact contact--address">
    <svg viewBox="0 0 10 10"><path d="M5 0.5 0 5h1.5v4.5h2.5V6.5h2v3h2.5V5H10z"/></svg>
    Lindenhof-Straße 22 | 80995 München
  </div>
  <div class="contact contact--fax">
    <svg viewBox="0 0 10 10"><rect x="2.5" y="0.5" width="5" height="3"/><rect x="0.5" y="3.5" width="9" height="4" rx="1"/><rect x="2.5" y="6.5" width="5" height="3"/></svg>
    089 - 47 21 3301
  </div>
  <div class="contact contact--mail">
    <svg viewBox="0 0 10 10"><path d="M0.5 2h9v6h-9z M0.5 2 5 5.5 9.5 2" fill="none" stroke="#fff" stroke-width="1"/></svg>
    info@kanzlei-zelliger.com
  </div>

  <div class="back-rule back-rule--lower"></div>

  <div class="contact contact--phone">
    <svg viewBox="0 0 10 10"><path d="M2.2 0.6 3.8 2.6 2.9 3.7c.7 1.4 1.9 2.6 3.4 3.4l1.1-.9 2 1.6-1 1.5C4.6 9.1.8 5.4.6 1.6z"/></svg>
    089 - 47 21 3300
  </div>
</section>

</body>
</html>
```